Creation of a construction/bricklaying business website

Following the template format of "Halloway 7", the following content would need to be included:
1. Landing page with 3 tiles that go to their own pages.
- Landing page to include background photo and description of services offered.
2. 3 tiles to include:
a) "Contact Us For A Free Quote or Friendly Discussion" Form (middle tile)
b) Case Studies and Testimonials
c) Certifications and Professional Membership
- Design logo to be used from previous SketchNestle project. Example of logo attached below, please access full JPG files from our account.

Target Market(s)

Prospective clients seeking construction work (bricklaying speciality)

Industry/Entity Type

Residential Construction

Coding

Coded - Design and coding required

Number of Pages Required

4 page

Font styles to use
Sans Serif

Colors

Designer to choose colors to be used in the design.

Requirements
Must have
• Following the template format of "Halloway 7", the following content would need to be included:
• 1. Landing parent page with 3 tiles that go to the 3 child pages.
• - Landing page to include background photo and description of services offered.
• 2. 3 tiles to include:
• a) "Contact Us For A Free Quote or Friendly Discussion" Form (middle tile)
• b) Case Studies and Testimonials (first tile / left side)
• c) Certifications and Professional Memberships (third tile / right side) (This should include logos of the relevant organisations being displayed. Specifically GQT and the Pillar Seal GQT).
• - Design logo to be used from previous SketchNestle project. Example of logo attached below, please access full JPG files from our account.
Nice to have
• Sleek and modern feel.
• Approachable in terms of how people can contact the company for a quote.
• Traditional pictures to give credibility and comfort around choosing this company.
Should not have
• Cheesy pictures
• Over-complicated
• Simple to use
• Easy URL domain name

```html
<!DOCTYPE html>
<html lang="en">
<head>
<meta charset="utf-8">
<title>R.T.Marsh Construction Ltd</title>
<link href="https://fonts.googleapis.com/css2?family=Jost:wght@400;500;600&family=Archivo:wght@500;600&display=swap" rel="stylesheet">
<style>
:root{
  --blue:#1454a6;
  --ink:#1b1b1b;
  --grey-text:#3a3a3a;
  --tile-grey:#e8ecec;
  --footer:#050505;
  --white:#ffffff;
  --icon-bg:#f1f1f1;
  --rule:#1e2a3c;
}
*{box-sizing:border-box;margin:0;padding:0}
html,body{width:986px;height:1200px;overflow:hidden;background:var(--white)}
body{font-family:"Jost",sans-serif;color:var(--ink)}
.page{position:relative;width:986px;height:1200px;overflow:hidden}
.hero{position:absolute;left:0;top:0;width:986px;height:481px}
.hero-photo{position:absolute;inset:0;background:
  linear-gradient(180deg,rgba(20,14,12,.55),rgba(20,14,12,.6)),
  linear-gradient(100deg,#5e3a2e 0%,#7a4a3a 30%,#6b5a52 55%,#4b4440 75%,#6a6660 100%)}
.top-contact{position:absolute;top:16px;display:flex;align-items:center;gap:8px;color:var(--white);font-size:12px;line-height:17px}
.top-contact.phone{left:133px}
.top-contact.email{left:671px}
.round-icon{width:31px;height:31px;border-radius:50%;background:var(--blue);display:flex;align-items:center;justify-content:center;flex:none}
.brand{position:absolute;left:0;width:986px;display:flex;justify-content:center;align-items:center;gap:10px;color:var(--blue);font-weight:500}
.brand-mark{background:var(--blue);flex:none}
.brand-hero{top:160px;font-size:30px;line-height:36px}
.brand-hero .brand-mark{width:22px;height:22px}
.hero-title{position:absolute;top:232px;left:0;width:986px;text-align:center;color:var(--white);font-family:"Archivo",sans-serif;font-weight:500;font-size:22.5px;line-height:26px}
.cta{position:absolute;left:426px;top:310px;width:132px;height:27px;background:var(--blue);color:var(--white);font-size:13px;line-height:27px;text-align:center}
.services{position:absolute;top:436px;left:0;width:986px}
.service{position:absolute;width:120px;text-align:center}
.service-badge{width:84px;height:84px;margin:0 auto;border-radius:50%;border:3px solid var(--blue);background:var(--icon-bg);display:flex;align-items:center;justify-content:center;box-shadow:0 10px 6px -8px rgba(0,0,0,.15)}
.service-name{margin-top:25px;font-family:"Archivo",sans-serif;font-weight:500;font-size:15.5px;line-height:18px;color:var(--grey-text)}
.intro{position:absolute;top:611px;left:136px;width:714px;text-align:center;font-size:12.5px;line-height:19.5px}
.intro p+p{margin-top:13px}
.tiles{position:absolute;top:726px;left:133px;width:720px;height:224px;display:flex}
.tile{width:240px;height:224px;text-align:center;padding-top:23px}
.tile.grey{background:var(--tile-grey)}
.tile-icon{height:56px;display:flex;justify-content:center;align-items:flex-end}
.tile-title{margin-top:12px;font-family:"Archivo",sans-serif;font-weight:500;font-size:11.5px;line-height:15.5px}
.tile-text{margin-top:11px;font-size:11.5px;line-height:17.5px;padding:0 6px}
.tile-link{display:inline-block;margin-top:10px;color:var(--blue);font-family:"Archivo",sans-serif;font-weight:500;font-size:11.5px;text-decoration:underline}
.footer{position:absolute;top:994px;left:0;width:986px;height:206px;background:var(--footer);color:var(--white)}
.brand-footer{top:30px;font-size:17px;line-height:22px}
.brand-footer .brand-mark{width:13px;height:13px}
.footer-item{position:absolute;top:88px;display:flex;align-items:center;gap:12px;font-size:11.5px;line-height:18px}
.footer-rule{position:absolute;top:140px;left:156px;width:674px;height:1px;background:var(--rule)}
.copyright{position:absolute;top:163px;left:156px;font-size:11.5px}
.social{position:absolute;top:155px;left:709px;display:flex;gap:4px}
.social span{width:25px;height:25px;border-radius:50%;background:var(--white);display:flex;align-items:center;justify-content:center}
</style>
</head>
<body>
<div class="page">
  <header class="hero">
    <div class="hero-photo" role="img" aria-label="Photo of a newly built red brick garden wall along a residential street"></div>
    <div class="top-contact phone">
      <span class="round-icon"><svg width="15" height="15" viewBox="0 0 24 24"><path fill="#fff" d="M6.6 10.8a15 15 0 0 0 6.6 6.6l2.2-2.2c.3-.3.7-.4 1-.2 1.1.4 2.3.6 3.6.6.6 0 1 .4 1 1V20c0 .6-.4 1-1 1A17 17 0 0 1 3 4c0-.6.4-1 1-1h3.5c.6 0 1 .4 1 1 0 1.2.2 2.4.6 3.6.1.3 0 .7-.2 1z"/></svg></span>
      <span>Call Us On<br>555.010.2468</span>
    </div>
    <div class="top-contact email">
      <span class="round-icon"><svg width="16" height="12" viewBox="0 0 16 12"><rect x=".5" y=".5" width="15" height="11" fill="none" stroke="#fff"/><path d="M.5.5 8 7l7.5-6.5" fill="none" stroke="#fff"/></svg></span>
      <span>Email Us On<br>info@rtmarshbuild.com</span>
    </div>
    <div class="brand brand-hero"><span class="brand-mark"></span><span>R.T.Marsh Construction Ltd</span></div>
    <h1 class="hero-title">R.T.Marsh Construction Ltd is a construction company that<br>has expertise and experience in the following areas</h1>
    <div class="cta">Contact Us Today &rarr;</div>
  </header>

  <section class="services">
    <div class="service" style="left:115px">
      <div class="service-badge"><svg width="44" height="40" viewBox="0 0 44 40" fill="none" stroke="#333" stroke-width="2"><path d="M4 18 20 6l16 12"/><rect x="8" y="16" width="24" height="18"/><rect x="12" y="22" width="6" height="6"/><rect x="22" y="22" width="6" height="12"/><path d="M4 38h36"/></svg></div>
      <div class="service-name">Extensions</div>
    </div>
    <div class="service" style="left:241px">
      <div class="service-badge"><svg width="46" height="42" viewBox="0 0 46 42"><path d="M3 21 23 4l20 17" fill="none" stroke="#333" stroke-width="4"/><path d="M9 20v20h28V20L23 8z" fill="#333"/><rect x="16" y="22" width="5" height="5" fill="#fff"/><rect x="25" y="22" width="5" height="5" fill="#fff"/><rect x="20" y="30" width="6" height="10" fill="#fff"/></svg></div>
      <div class="service-name">New build /<br>New houses</div>
    </div>
    <div class="service" style="left:375px">
      <div class="service-badge"><svg width="50" height="36" viewBox="0 0 50 36" fill="#333"><rect x="0" y="0" width="22" height="6"/><rect x="0" y="8" width="50" height="6"/><rect x="0" y="16" width="50" height="6"/><rect x="0" y="24" width="50" height="6"/><path d="M12 8v6M25 8v6M38 8v6M6 16v6M19 16v6M32 16v6M44 16v6M12 24v6M25 24v6M38 24v6" stroke="#f1f1f1" stroke-width="1.5"/></svg></div>
      <div class="service-name">Garden walls</div>
    </div>
    <div class="service" style="left:495px">
      <div class="service-badge"><svg width="44" height="40" viewBox="0 0 44 40" fill="none" stroke="#333" stroke-width="2"><rect x="2" y="2" width="28" height="34"/><path d="M2 10h28M2 19h28M2 28h28M12 2v8M22 10v9M12 19v9M22 28v8"/><path d="m28 22 12 12-6 2z" fill="#333"/></svg></div>
      <div class="service-name">Plastering</div>
    </div>
    <div class="service" style="left:622px">
      <div class="service-badge"><svg width="46" height="40" viewBox="0 0 46 40" fill="#333"><path d="M8 2v10" stroke="#333" stroke-width="2"/><path d="m4 12h8l-4 10z"/><rect x="14" y="20" width="10" height="5"/><rect x="26" y="20" width="10" height="5"/><rect x="8" y="27" width="10" height="5"/><rect x="20" y="27" width="10" height="5"/><rect x="32" y="27" width="10" height="5"/><rect x="14" y="34" width="22" height="5"/></svg></div>
      <div class="service-name">Brickwork</div>
    </div>
    <div class="service" style="left:751px">
      <div class="service-badge"><svg width="46" height="42" viewBox="0 0 46 42" fill="#333"><rect x="6" y="2" width="10" height="3"/><rect x="10" y="5" width="2" height="18"/><path d="M5 22h12v12a6 6 0 0 1-12 0z"/><path d="M20 40l8-14 6 6 4-3 6 11z"/></svg></div>
      <div class="service-name">Groundworks</div>
    </div>
  </section>

  <section class="intro">
    <p>We pride ourselves on attention to detail, pride in our completed project and client satisfaction. We believe in full transparency and this is reflected in the jobs we quote for you. We break down each step with both labour and materials cost so you can see exactly what you are paying for.</p>
    <p>Feel free to get in touch and we can talk through what you are looking to achieve.</p>
  </section>

  <section class="tiles">
    <article class="tile grey">
      <div class="tile-icon"><svg width="76" height="52" viewBox="0 0 76 52"><rect x="32" y="2" width="40" height="48" fill="#fff" stroke="#1454a6" stroke-width="2"/><path d="M38 14h28M38 20h28M38 26h18M38 32h18" stroke="#1454a6" stroke-width="2"/><circle cx="60" cy="34" r="6" fill="#fff" stroke="#333" stroke-width="2"/><ellipse cx="14" cy="36" rx="12" ry="9" fill="#1454a6"/><ellipse cx="26" cy="28" rx="8" ry="6" fill="#444"/></svg></div>
      <h2 class="tile-title">Case Studies and<br>Testimonials</h2>
      <p class="tile-text">Ut wisi enim ad minim veniam, quis nostrud exerci tation ullamcorper suscipit lobortis nisl ut aliquip ex ea commodo consequat.</p>
      <a class="tile-link">Read More</a>
    </article>
    <article class="tile">
      <div class="tile-icon"><svg width="50" height="54" viewBox="0 0 50 54"><path d="M8 2h30l10 10v40H8z" fill="#fff" stroke="#1454a6" stroke-width="3"/><path d="M20 24h22M20 32h22M20 40h22" stroke="#1454a6" stroke-width="2"/><path d="M12 8c0 6 4 10 10 10" fill="none" stroke="#333" stroke-width="3"/><path d="m2 42 5 8 9-16" fill="none" stroke="#333" stroke-width="3"/></svg></div>
      <h2 class="tile-title">Contact Us For A<br>Free Quote</h2>
      <p class="tile-text">Ut wisi enim ad minim veniam, quis nostrud exerci tation ullamcorper suscipit lobortis nisl ut aliquip ex ea commodo consequat.</p>
      <a class="tile-link">Contact Us</a>
    </article>
    <article class="tile grey">
      <div class="tile-icon"><svg width="70" height="52" viewBox="0 0 70 52" role="img" aria-label="Membership badges: GQT and Pillar Seal GQT"><rect x="0" y="0" width="30" height="52" fill="#c8102e"/><rect x="36" y="0" width="34" height="52" fill="#c8102e"/></svg></div>
      <h2 class="tile-title">Certifications and Professional<br>Memberships</h2>
      <p class="tile-text">Ut wisi enim ad minim veniam, quis nostrud exerci tation ullamcorper suscipit lobortis nisl ut aliquip ex ea commodo consequat.</p>
      <a class="tile-link">Know More</a>
    </article>
  </section>

  <footer class="footer">
    <div class="brand brand-footer"><span class="brand-mark"></span><span>R.T.Marsh Construction Ltd</span></div>
    <div class="footer-item" style="left:156px">
      <span class="round-icon"><svg width="12" height="16" viewBox="0 0 12 16"><path d="M6 0a6 6 0 0 0-6 6c0 4.5 6 10 6 10s6-5.5 6-10a6 6 0 0 0-6-6z" fill="#fff"/><circle cx="6" cy="6" r="2.2" fill="#1454a6"/></svg></span>
      <span>Street Name, City Name<br>State Zipcode</span>
    </div>
    <div class="footer-item" style="left:421px">
      <span class="round-icon"><svg width="15" height="15" viewBox="0 0 24 24"><path fill="#fff" d="M6.6 10.8a15 15 0 0 0 6.6 6.6l2.2-2.2c.3-.3.7-.4 1-.2 1.1.4 2.3.6 3.6.6.6 0 1 .4 1 1V20c0 .6-.4 1-1 1A17 17 0 0 1 3 4c0-.6.4-1 1-1h3.5c.6 0 1 .4 1 1 0 1.2.2 2.4.6 3.6.1.3 0 .7-.2 1z"/></svg></span>
      <span>Call Us On :<br>555.010.2468</span>
    </div>
    <div class="footer-item" style="left:639px">
      <span class="round-icon"><svg width="16" height="12" viewBox="0 0 16 12"><rect x=".5" y=".5" width="15" height="11" fill="none" stroke="#fff"/><path d="M.5.5 8 7l7.5-6.5" fill="none" stroke="#fff"/></svg></span>
      <span>Email<br>info@rtmarshbuild.com</span>
    </div>
    <div class="footer-rule"></div>
    <p class="copyright">Copyright ©2018 R.T.Marsh Construction Ltd. All Rights Reserved.</p>
    <div class="social" aria-label="Social links">
      <span><svg width="13" height="13" viewBox="0 0 14 14" fill="none" stroke="#1454a6" stroke-width="1.4"><circle cx="7" cy="7" r="6"/><path d="M1 7h12M7 1c2.5 3 2.5 9 0 12M7 1c-2.5 3-2.5 9 0 12"/></svg></span>
      <span><svg width="13" height="12" viewBox="0 0 14 13"><path d="M1 1h12v8H6l-3 3V9H1z" fill="#1454a6"/></svg></span>
      <span><svg width="13" height="13" viewBox="0 0 14 14"><circle cx="3" cy="7" r="2" fill="#1454a6"/><circle cx="11" cy="3" r="2" fill="#1454a6"/><circle cx="11" cy="11" r="2" fill="#1454a6"/><path d="M3 7 11 3M3 7l8 4" stroke="#1454a6" stroke-width="1.3"/></svg></span>
      <span><svg width="13" height="10" viewBox="0 0 16 12"><rect x=".5" y=".5" width="15" height="11" fill="none" stroke="#1454a6" stroke-width="1.4"/><path d="M.5.5 8 7l7.5-6.5" fill="none" stroke="#1454a6" stroke-width="1.4"/></svg></span>
    </div>
  </footer>
</div>
</body>
</html>
```